VELTAR WEBSITE

need to create a new website for VELTAR ltd
the company deals with all aspects of safety products & safety wear
we need a simple website to show
ideas can be taken from following website whose products we shall distribute in kenya
www.kwr.co.uk
www.dorvik.eu
www.brimtoolsupplyco.com
www.gardvalewerks.co.za

we need following tabs
1) home - basic company information
2) products - broken down to following categories ie gloves, head protection, ear protection, mouth protection, foot protection
3) contacts

the company profile is a reputable company dealing with all aspects of safety, HSE (health and safety equipment), and PPE (personal protective equipment)

the website should have the dorvik logo for which we are an authorized distributor.
the dorvi industrial range writeup can be picked from their website
Updates

Dear Designers, i shall be able to choose a final design in 2 weeks, sorry i have not been able to finalise this due to a personal reason

Target Market(s)

the buyers are all types of industry who care for their employees safety

Industry/Entity Type

Industrial

Requirements
Must have
• clean look, fresh look, user freindly
Nice to have
• clear images, quick links etc

```html
<!DOCTYPE html>
<html lang="en">
<head>
<meta charset="utf-8">
<title>Veltar Limited – Safety Products &amp; Safety Wear</title>
<link href="https://fonts.googleapis.com/css2?family=Source+Sans+3:ital,wght@0,400;0,600;0,700;1,400&family=Arimo:wght@400;700&display=swap" rel="stylesheet">
<style>
:root{
  --ink:#1f2a33;
  --text:#333;
  --muted:#7a7a7a;
  --gold:#e6b32c;
  --gold-dark:#c9971b;
  --frame:#d9d9d9;
  --footer:#2b2b2b;
  --footer-base:#1c1c1c;
  --footer-text:#cfcfcf;
  --footer-head:#a9a9a9;
  --rule:#4a4a4a;
}
*{box-sizing:border-box;margin:0;padding:0}
html,body{width:929px;height:1200px;overflow:hidden;background:#fff}
body{position:relative;font-family:"Source Sans 3",sans-serif;color:var(--text)}
.topline{position:absolute;left:0;top:0;width:929px;height:3px;background:var(--ink)}
.abs{position:absolute}

/* header */
.brand{left:110px;top:30px;display:flex;align-items:center;gap:8px}
.brand-mark{width:22px;height:22px;background:var(--gold)}
.brand-name{font-family:"Arimo",sans-serif;font-weight:700;font-size:28px;color:var(--ink);letter-spacing:1px}
.call{right:110px;top:28px;font-size:14px;font-weight:600;color:var(--ink);display:flex;align-items:center;gap:5px}
.call b{font-size:18px;font-weight:600;letter-spacing:1px;margin-left:3px}
.search{left:658px;top:65px;width:161px;height:19px;border:1px solid #c9c9c9;border-radius:5px;background:#f6f6f6;font-size:9px;font-style:italic;color:#aaa;padding:3px 9px}
.search svg{position:absolute;right:6px;top:3px}

/* navigation */
.nav{left:110px;top:104px;width:710px;height:28px;background:var(--gold);border:2px solid #fff;box-shadow:0 2px 5px rgba(0,0,0,.25);display:flex;justify-content:space-around;align-items:center}
.nav a{font-size:11px;font-weight:600;color:#3a2e10;text-decoration:none}

/* slider */
.slider{left:109px;top:140px;width:712px;height:302px;border:1px solid var(--frame);background:#fff;box-shadow:0 8px 10px -6px rgba(0,0,0,.2)}
.slide-photo{position:absolute;left:3px;top:3px;width:704px;height:294px;background:linear-gradient(90deg,#b8c5cf 0%,#d7e0e6 30%,#c3ccd3 60%,#a9b3ba 100%)}
.slide-tabs{position:absolute;left:292px;top:275px;width:126px;height:22px;background:var(--gold);clip-path:polygon(8% 0,92% 0,100% 100%,0 100%);display:flex;justify-content:center;align-items:center;gap:9px}
.slide-tabs i{width:11px;height:11px;border-radius:50%;background:var(--gold-dark)}
.slide-tabs i:first-child{background:var(--ink)}

/* welcome */
.welcome{left:110px;top:459px;width:710px;text-align:center}
.welcome h1{font-family:"Arimo",sans-serif;font-size:16px;font-weight:400;color:var(--ink)}
.welcome h1 strong{font-weight:700}
.welcome p{font-size:10.5px;line-height:17.5px;color:var(--text);margin-top:7px}
.section-title{left:110px;width:710px;text-align:center;font-size:16px;font-weight:600;color:var(--ink)}

/* products */
.product{width:197px;top:592px}
.product-photo{height:83px;border:1px solid var(--frame);padding:3px}
.product-photo div{width:100%;height:100%}
.product p{font-family:"Arimo",sans-serif;font-size:9px;line-height:16px;color:#222;margin-top:12px}
.product a{display:block;font-family:"Arimo",sans-serif;font-size:10px;color:#222;text-decoration:none;margin-top:5px}
.band{left:110px;top:772px;width:710px;height:14px;background:linear-gradient(#f2f2f2,#fff)}

/* testimonials */
.quote{width:215px}
.quote .mark{position:absolute;left:0;top:0;font-family:Georgia,serif;font-size:30px;line-height:1;color:#bbb}
.quote .avatar{position:absolute;left:20px;top:4px;width:60px;height:54px;border:1px solid var(--frame);padding:2px}
.quote .avatar div{width:100%;height:100%;background:linear-gradient(#e4e8ec,#9aa3ab)}
.quote .lead{position:absolute;left:92px;top:0;width:130px;font-size:8.5px;font-style:italic;line-height:14.5px;color:#666}
.quote .body{position:absolute;left:20px;top:64px;width:210px;font-size:8.5px;font-style:italic;line-height:14.5px;color:#666}
.quote .author{position:absolute;left:20px;top:117px;font-size:9px;font-weight:700;color:#555}

/* footer */
.footer{left:0;top:980px;width:929px;height:175px;background:var(--footer)}
.fcol{top:999px}
.fcol h3{font-size:14px;font-weight:400;color:var(--footer-head);margin-bottom:8px;letter-spacing:.2px}
.fcol li{list-style:none;font-size:10px;line-height:20.3px;color:var(--footer-text)}
.fcol p{font-size:9.5px;line-height:16px;color:var(--footer-text)}
.fcol .posted{font-size:9px;margin:7px 0 12px}
.vrule{top:1000px;width:1px;height:142px;background:var(--rule)}
.social li{display:flex;align-items:center;gap:10px;line-height:27px}
.social span{width:22px;height:22px;border-radius:50%;background:#f2f2f2}
.base{left:0;top:1155px;width:929px;height:45px;background:var(--footer-base)}
.copy{left:111px;top:1171px;font-size:8.5px;color:#8d8d8d}
.partner{left:726px;top:1162px;font-size:22px;font-weight:700;color:#9a9a9a}
</style>
</head>
<body>
<div class="topline"></div>

<header>
  <div class="abs brand"><span class="brand-mark"></span><span class="brand-name">VELTAR</span></div>
  <div class="abs call">
    <svg width="15" height="11" viewBox="0 0 15 11" aria-hidden="true"><path d="M1 4c0-2 3-3 6.5-3S14 2 14 4l-3 1-1-2H5L4 5 1 4zM3 6h9l1 5H2z" fill="#1f2a33"/></svg>
    Call Us: <b>11 111 1111</b>
  </div>
  <div class="abs search">Search...
    <svg width="13" height="12" viewBox="0 0 13 12" aria-hidden="true"><circle cx="5" cy="5" r="3.6" fill="none" stroke="#1f2a33" stroke-width="1.6"/><path d="M7.6 7.4l4 3.6" stroke="#1f2a33" stroke-width="2.2"/></svg>
  </div>
  <nav class="abs nav">
    <a>HOME</a><a>ABOUT US</a><a>PRODUCTS</a><a>CLIENTS</a><a>AGENCIES</a><a>PRODUCTS</a><a>CONTACT US</a>
  </nav>
</header>

<section class="abs slider">
  <div class="slide-photo" role="img" aria-label="Two engineers in yellow hard hats on a construction site"></div>
  <div class="slide-tabs"><i></i><i></i><i></i><i></i></div>
</section>

<section class="abs welcome">
  <h1>Welcome To&nbsp; <strong>Veltar Limited</strong></h1>
  <p>Sed ut perspiciatis unde omnis iste natus error sit voluptatem accusantium doloremque laudantium, totam rem aperiam, eaque<br>ipsa quae ab illo inventore veritatis et quasi architecto beatae vitae dicta sunt explicabo.<br>Nemo enim voluptatem sequi nesciunt.</p>
</section>

<h2 class="abs section-title" style="top:550px">Products &amp; Services</h2>

<article class="abs product" style="left:110px">
  <div class="product-photo"><div role="img" aria-label="Welder in protective gloves and mask" style="background:linear-gradient(90deg,#2a2e3a,#c9a22a 40%,#b0302a 75%,#1a1a1a)"></div></div>
  <p>Sed ut perspiciatis unde omnis iste natus error sit voluptatem accusantium doloremque laudantium, totam rem aperiam</p>
  <a>&gt;&gt; Read More</a>
</article>
<article class="abs product" style="left:366px">
  <div class="product-photo"><div role="img" aria-label="Yellow and white safety helmets" style="background:radial-gradient(circle at 45% 50%,#f0c020 0,#f3d560 30%,#fff 62%)"></div></div>
  <p>Sed ut perspiciatis unde omnis iste natus error sit voluptatem accusantium doloremque laudantium, totam rem aperiam</p>
  <a>&gt;&gt; Read More</a>
</article>
<article class="abs product" style="left:622px">
  <div class="product-photo"><div role="img" aria-label="Worker wearing clear safety glasses" style="background:linear-gradient(90deg,#e8e8e8,#e2cbbb 60%,#c9a894)"></div></div>
  <p>Sed ut perspiciatis unde omnis iste natus error sit voluptatem accusantium doloremque laudantium, totam rem aperiam</p>
  <a>&gt;&gt; Read More</a>
</article>

<div class="abs band"></div>
<h2 class="abs section-title" style="top:786px">Customer Testimonials</h2>

<figure class="abs quote" style="left:110px;top:834px">
  <span class="mark">“</span>
  <div class="avatar"><div role="img" aria-label="Business partners shaking hands"></div></div>
  <p class="lead">Nunc tempus felis vitae urna. Vivamus porttitor, neque at volut-pat rutrum, purus nisi eleifend libero, a tempus libero lectus</p>
  <p class="body">Morbi eget arcu. Morbi porta, libero id ullamcorper non-ummy, nibh ligula pulvinar metus, eget consectetuer augue nisi quis lacus. Ut ac mi quis lacus. <b style="color:#bbb;font-size:13px">”</b></p>
  <p class="author">By Author Name</p>
</figure>
<figure class="abs quote" style="left:355px;top:827px">
  <span class="mark">“</span>
  <div class="avatar"><div role="img" aria-label="Customer portrait"></div></div>
  <p class="lead">Nunc tempus felis vitae urna. Vivamus porttitor, neque at volut-pat rutrum, purus nisi eleifend libero, a tempus libero lectus</p>
  <p class="body">Morbi eget arcu. Morbi porta, libero id ullamcorper non-ummy, nibh ligula pulvinar metus, eget consectetuer augue nisi quis lacus. Ut ac mi quis lacus. <b style="color:#bbb;font-size:13px">”</b></p>
  <p class="author">By Author Name</p>
</figure>
<figure class="abs quote" style="left:596px;top:830px">
  <span class="mark">“</span>
  <div class="avatar"><div role="img" aria-label="Customer portrait"></div></div>
  <p class="lead">Nunc tempus felis vitae urna. Vivamus porttitor, neque at volut-pat rutrum, purus nisi eleifend libero, a tempus libero lectus</p>
  <p class="body">Morbi eget arcu. Morbi porta, libero id ullamcorper non-ummy, nibh ligula pulvinar metus, eget consectetuer augue nisi quis lacus. Ut ac mi quis lacus. <b style="color:#bbb;font-size:13px">”</b></p>
  <p class="author">By Author Name</p>
</figure>

<footer>
  <div class="abs footer"></div>
  <div class="abs fcol" style="left:111px"><h3>COMPANY</h3><ul><li>Company Overview</li><li>About Us</li><li>Services Provide</li><li>Our Process</li><li>Our Clients</li></ul></div>
  <div class="abs vrule" style="left:240px"></div>
  <div class="abs fcol" style="left:276px"><h3>WHAT WE DO</h3><ul><li>Value proposition</li><li>Our work</li><li>Testimonials</li><li>Faq</li><li>Contact us</li></ul></div>
  <div class="abs vrule" style="left:402px"></div>
  <div class="abs fcol" style="left:438px;width:220px"><h3>CHIRPER FEED</h3>
    <p>Nunc tempus felis vitae urna. Vivamus porttitor, g, purus nisi eleifend libero, a tempus</p><p class="posted">Posted 3 hours ago</p>
    <p>Nunc tempus felis vitae urna. Vivamus porttitor, g, purus nisi eleifend libero, a tempus</p><p class="posted">Posted 3 hours ago</p>
  </div>
  <div class="abs vrule" style="left:674px"></div>
  <div class="abs fcol social" style="left:714px"><h3>GET CONNECTED</h3><ul><li><span></span>Facepage</li><li><span></span>Chirper</li><li><span></span>Linkwork</li><li><span></span>RSS</li></ul></div>
  <div class="abs base"></div>
  <p class="abs copy">© 2013 Company Name.&nbsp; All right reserved.&nbsp; Term of Use</p>
  <p class="abs partner">Dorvik</p>
</footer>
</body>
</html>
```